Tech business card design

We need an amazing business card design for our new business 'Pexla' a marketing tech startup based in Sydney, Australia. We provide an online marketplace for businesses to search and buy advertising media, connect with service providers and learn more about marketing. We wish to communicate 'cool tech', reliability and professionalism and design based around our logo.

Target Market(s)

Business Owners

Contact Information for Business Card

Name
Position
Email Address
Website
Phone Number

Font styles to use
Other font styles liked:
• Avenir & Avenir Next

Colors

Designer to choose colors to be used in the design.

```html
<!DOCTYPE html>
<html lang="en">
<head>
<meta charset="utf-8">
<title>Pexla Business Card</title>
<link rel="stylesheet" href="https://fonts.googleapis.com/css2?family=Montserrat:wght@400;500;800&display=swap">
<style>
  :root {
    --bg-top: #4a4a4a;
    --bg-bottom: #2a2a2a;
    --card: #2b2b2b;
    --ink: #ffffff;
    --ink-soft: #d9d9d9;
    --rule: #cfcfcf;
  }
  * { margin: 0; padding: 0; box-sizing: border-box; }
  html, body { width: 1200px; height: 1000px; overflow: hidden; }
  body {
    background: radial-gradient(ellipse at 50% 30%, var(--bg-top), var(--bg-bottom));
    font-family: "Montserrat", sans-serif;
    position: relative;
  }
  .card {
    position: absolute;
    left: 270px;
    width: 660px;
    height: 380px;
    background: var(--card);
    border-radius: 22px;
    box-shadow: 0 14px 40px rgba(0,0,0,0.45);
  }
  .card--front { top: 60px; }
  .card--back { top: 500px; }

  .wordmark {
    color: var(--ink);
    font-weight: 800;
    letter-spacing: -1px;
    line-height: 1;
  }
  .card--front .wordmark {
    position: absolute;
    left: 0; right: 0; top: 130px;
    text-align: center;
    font-size: 120px;
  }
  .card--back .wordmark {
    position: absolute;
    left: 50px; top: 150px;
    font-size: 76px;
  }
  .divider {
    position: absolute;
    left: 300px; top: 105px;
    width: 1.5px; height: 175px;
    background: var(--rule);
  }
  .details {
    position: absolute;
    left: 330px; top: 112px;
    color: var(--ink);
  }
  .details__name { font-size: 24px; font-weight: 500; }
  .details__role { font-size: 15px; color: var(--ink-soft); margin-top: 2px; margin-bottom: 22px; }
  .contact {
    display: flex; align-items: center; gap: 8px;
    font-size: 17px; margin-bottom: 8px;
  }
  .contact svg { width: 22px; height: 22px; flex: none; }
</style>
</head>
<body>
  <section class="card card--front">
    <div class="wordmark">pexla</div>
  </section>

  <section class="card card--back">
    <div class="wordmark">pexla</div>
    <div class="divider"></div>
    <div class="details">
      <div class="details__name">Marcus Hale</div>
      <div class="details__role">Managing Director</div>
      <div class="contact">
        <svg viewBox="0 0 22 22" fill="none" stroke="#fff" stroke-width="1.3"><circle cx="11" cy="11" r="10"/><rect x="8" y="5.5" width="6" height="11" rx="1"/></svg>
        <span>800-555-0142</span>
      </div>
      <div class="contact">
        <svg viewBox="0 0 22 22" fill="none" stroke="#fff" stroke-width="1.3"><circle cx="11" cy="11" r="10"/><rect x="6" y="7.5" width="10" height="7"/><path d="M6 7.5l5 4 5-4"/></svg>
        <span>marcus@pexla.com</span>
      </div>
      <div class="contact">
        <svg viewBox="0 0 22 22" fill="none" stroke="#fff" stroke-width="1.3"><circle cx="11" cy="11" r="10"/><circle cx="11" cy="11" r="5.5"/><path d="M5.5 11h11M11 5.5v11"/></svg>
        <span>www.pexla.com</span>
      </div>
    </div>
  </section>
</body>
</html>
```